A website where experts collaborate on your project

I am building a new website where experts (yes, like designers) collaborate on projects with the project owner. More minds = more collaboration = better end product. Please see Pelmora(dot)com for a quick landing page I created for collaborating on presentations (although there will be many project types offered)

I am looking for a DESIGNER LONG TERM, but for now, just need initial mock ups to show the web programmers.

I have 21 Word documents loosely designed, what I would like to see here is a theme. Please DO NOT GO OFF WHAT YOU CURRENTLY SEE AT PELMORA. What is up now is only a quick landing page.

You can view a Word doc of the homepage here:
https://www.filevanta.com/s/qx83kdm2/home.docx?dl=0

WHAT AM I LOOKING FOR?
A clean, well designed theme.

Here is a link to the logo:
https://www.filevanta.com/s/mr47tpz9/logo%20-%20horizontal.tif?dl=0
-----------------------------------------
Here are a few sites I like the design of and what I like about them:
www.quenbrook.com-all around my favorite, beautiful graphics, clean layout, bold use of colors on a dark background
Ravelto.com- clean layout, The use of humans and bubble style elements.
Mintharbor.com :) clean, bold, unique pop art style but professional
plumevault.com - From the unique colors and artwork and the ability of that art to not interfere with the important elements of the site
sparkwidgets.com-clean, nice colors, well organized and separated sections.
www.dunmereco.com-love the font, use of colors and sectionalized style

All in all, I am not picky and open to so many styles. I would ultimately like the designer I pick to design all 21 pages.
Updates

Hello everyone,Moving forward, I would like you all to pay special attention to the section in my brief titled "Here are a few sites I like the design of and what I like about them". Please see below, I handpicked each one of these as sites I really like. Thank you.Here are a few sites I like the design of and what I like about them:Ravelto.com- clean layout, The use of humans and bubble style elements.Mintharbor.com :) clean, bold, unique pop art style but professionalwriteraccess.com - From the unique colors and artwork and the ability of that art to not interfere with the important elements of the sitegrowthgeeks.com-clean, nice colors, well organized and separated sections.www.dunmereco.com-love the font, use of colors and sectionalized stylewww.quenbrook.com-beautiful graphics, clean layout, bold use of colors----------------------------------------- Added Tuesday, November 24, 2015

I updated the homepage, you can see it here:https://www.dropbox.com/s/kwlkbsookq3cg2m/1new%20homepage.docx?dl=0I am modeling it after my favorite designed site: triplelift.comI love the dark colors with the orange glowing style boldness of the buttons. It's real clean too. Added Tuesday, November 24, 2015

Target Market(s)

small business owners, marketers, freelancer writers, graphic designers,

Industry/Entity Type

Building

Number of Pages Required

5+ page

Requirements
Must have
• I can't think of anything the project must have.
Nice to have
• WHAT AM I LOOKING FOR?
• A clean, well designed theme. I had a designer do a bit of work putting elements together, I found it to be very plain, but I like the Application Page (https://www.filevanta.com/s/jb19ckr3/Pelmora-Website.ai?dl=0)
• Here is a link to the logo:
• https://www.filevanta.com/s/mr47tpz9/logo%20-%20horizontal.tif?dl=0
• Here are a few sites I like the design of and what I like about them:
• Ravelto.com- clean layout, The use of humans and bubble style elements.
• Mintharbor.com :) clean, bold, unique pop art style but professional
• plumevault.com - From the unique colors and artwork and the ability of that art to not interfere with the important elements of the site
• sparkwidgets.com-clean, nice colors, well organized and separated sections.
• www.dunmereco.com-love the font, use of colors and sectionalized style
• www.quenbrook.com-beautiful graphics, clean layout, bold use of colors
• -----------------------------------------
Should not have
• out of the boxed, templated style website. I want this site to be memorable and not look like a thousand others

```html
<!DOCTYPE html>
<html lang="en">
<head>
<meta charset="utf-8">
<title>Pelmora – Crowd Projects</title>
<link href="https://fonts.googleapis.com/css2?family=Questrial&family=Open+Sans:ital,wght@0,400;0,600;1,400&display=swap" rel="stylesheet">
<style>
  :root{
    --orange:#f7941d;
    --orange-soft:#f6a948;
    --teal:#3aa6c4;
    --ink:#2a2a2a;
    --text:#555;
    --muted:#8a8a8a;
    --line:#e2e2e2;
    --panel:#f4f4f4;
    --card:#f6f6f6;
    --footer:#2b2b2b;
    --white:#fff;
  }
  *{box-sizing:border-box;margin:0;padding:0}
  html,body{width:692px;height:1200px;overflow:hidden;background:var(--white)}
  body{position:relative;font-family:"Open Sans",Arial,sans-serif;color:var(--text)}
  .abs{position:absolute}
  .display{font-family:"Questrial","Open Sans",sans-serif}

  /* header */
  .site-header{left:0;top:0;width:692px;height:77px;border-top:1px solid #d0d0d0;background:var(--white)}
  .brand{left:57px;top:38px;display:flex;align-items:center;gap:6px}
  .brand-name{font-family:"Questrial",sans-serif;font-size:17px;color:var(--orange)}
  .brand-dot{width:14px;height:14px;border-radius:50%;background:var(--orange)}
  .search{left:545px;top:12px;width:90px;height:20px;border:1px solid #f0c58a;border-radius:10px;font-size:6.5px;color:#aaa;padding:5px 8px}
  .search-toggle{right:-1px;top:-1px;width:20px;height:20px;border-radius:50%;border:1px solid var(--orange)}
  .nav{top:48px;font-family:"Questrial",sans-serif;font-size:9.5px;color:var(--ink)}
  .nav.active{color:var(--orange)}
  .help{left:612px;top:42px;width:25px;height:21px;border:1.5px solid var(--orange);border-radius:50%;color:var(--orange);font-size:11px;font-weight:600;text-align:center;line-height:18px}

  /* hero */
  .hero{left:0;top:77px;width:692px;height:309px;background:linear-gradient(100deg,#3b3530 0%,#5c5048 40%,#6e655d 70%,#4c4640 100%)}
  .hero-title{left:56px;top:118px;font-size:31px;color:var(--white)}
  .hero-sub{left:58px;top:158px;font-size:14.5px;font-style:italic;color:var(--white);line-height:21px;font-weight:400}
  .btn{background:var(--orange);color:var(--white);text-align:center;font-family:"Questrial",sans-serif}
  .hero-cta{left:57px;top:292px;width:106px;height:27px;font-size:9.5px;line-height:27px}
  .hero-dot{top:340px;width:15px;height:15px;border:1px solid rgba(255,255,255,.6);border-radius:50%}

  /* filters */
  .filters{left:59px;top:413px;width:159px;height:398px;background:var(--panel)}
  .filters-head{left:0;top:0;width:159px;height:31px;font-size:12px;line-height:31px;padding-left:13px;text-align:left;border:1px solid #e7872a}
  .filters-head-icon{right:13px;top:9px;width:13px;height:13px;border:1.2px solid var(--white);border-radius:50%}
  .price-label{left:10px;top:48px;font-size:11px;color:var(--ink);font-family:"Questrial",sans-serif}
  .price-tag{left:106px;top:42px;width:24px;height:15px;border-radius:8px;background:var(--orange);color:var(--white);font-size:6.5px;text-align:center;line-height:15px}
  .slider{left:10px;top:66px;width:137px;height:8px;border-radius:4px;background:#333;overflow:hidden}
  .slider-fill{left:0;top:0;width:105px;height:8px;background:var(--orange)}
  .price-min{left:12px;top:78px;font-size:7px;color:var(--ink)}
  .filter-row{left:12px;width:134px;height:32px;border-top:1px dotted #bbb;font-size:8px;color:var(--ink);padding:10px 0 0 17px}
  .plus{position:absolute;right:1px;top:11px;width:9px;height:9px;border:1px solid #999;border-radius:50%;font-size:8px;line-height:7px;text-align:center;color:#777}
  .save{left:59px;top:821px;width:159px;height:28px;font-size:11px;line-height:28px}

  /* projects */
  .section-title{left:248px;top:410px;font-size:14px;color:var(--ink)}
  .section-title span{color:var(--orange)}
  .sort{left:495px;top:409px;width:140px;height:23px;border:1px solid var(--line);font-size:7.5px;color:var(--ink)}
  .sort-label{left:0;top:0;width:50px;height:21px;background:#ececec;line-height:21px;text-align:center}
  .sort-value{left:50px;top:0;width:88px;height:21px;background:var(--white);line-height:23px;padding-left:14px}
  .sort-menu{left:545px;top:432px;width:90px;height:66px;background:var(--white);border:1px solid var(--line);font-size:7.5px;color:var(--ink);z-index:2}
  .sort-item{height:22px;line-height:22px;padding-left:11px}
  .sort-item.is-active{background:var(--orange);color:var(--white)}

  .card{left:249px;width:386px;border:1px solid #ececec;background:var(--white)}
  .card.is-first{background:var(--card)}
  .card-photo{left:10px;top:14px;width:100px;height:100px;border-radius:50%;border:4px solid #e6e6e6}
  .card-wedge{left:44px;top:92px}
  .card-price{left:68px;top:87px;width:36px;height:36px;border-radius:50%;background:var(--white);border:1.5px solid var(--orange);color:var(--orange);font-size:9px;line-height:10px;text-align:center;padding-top:7px}
  .card-price b{font-weight:400;color:#333}
  .card-title{left:125px;top:20px;font-size:11px;color:var(--ink);font-family:"Questrial",sans-serif;white-space:nowrap}
  .card-time{left:125px;top:38px;font-size:7.5px;color:var(--orange)}
  .card-body{left:125px;top:56px;width:252px;font-size:6.3px;line-height:15px;color:#777}

  .pager{left:456px;top:918px;font-size:7.5px;font-weight:600;color:var(--ink);display:flex;gap:11px}
  .pager .is-current{color:var(--orange)}
  .pager-line{left:474px;top:934px;width:160px;height:1px;background:linear-gradient(90deg,transparent,#bbb,transparent)}

  /* testimonials */
  .testimonials{left:0;top:958px;width:692px;height:198px;background:linear-gradient(90deg,#f1a447 0%,#f4ad57 50%,#eeb068 75%,#f0a650 100%)}
  .t-title{left:0;top:30px;width:692px;text-align:center;font-size:16px;color:var(--white)}
  .t-quote{left:0;top:62px;width:692px;text-align:center;font-size:12.5px;font-style:italic;color:var(--white);line-height:21px}
  .t-mark{font-size:22px;color:var(--white);font-family:Georgia,serif;font-style:normal}
  .t-avatar{left:288px;top:116px;width:48px;height:48px;border-radius:50%;border:3px solid var(--white);background:linear-gradient(#dde3e6,#9aa7ad)}
  .t-name{left:345px;top:120px;font-size:9px;font-weight:600;color:var(--white)}
  .t-role{left:345px;top:135px;font-size:6.5px;color:var(--white)}
  .t-stars{left:345px;top:145px}

  /* footer */
  .footer{left:0;top:1156px;width:692px;height:44px;background:var(--footer)}
  .footer-links{left:57px;top:17px;font-size:7.5px;color:#9a9a9a}
  .social{top:14px;width:17px;height:17px;border-radius:50%;background:#555}
</style>
</head>
<body>

<header class="site-header abs">
  <div class="brand abs"><span class="brand-name">pelmora</span><span class="brand-dot"></span></div>
  <div class="search abs">Browse....<span class="search-toggle abs"><svg width="18" height="18" viewBox="0 0 18 18"><path d="M6 8l3 3 3-3" fill="none" stroke="#f7941d" stroke-width="1.2"/></svg></span></div>
  <span class="nav abs active" style="left:324px">Home</span>
  <span class="nav abs" style="left:372px">Projects</span>
  <span class="nav abs" style="left:428px">How it works</span>
  <span class="nav abs" style="left:503px">Plans</span>
  <span class="nav abs" style="left:548px">My Account</span>
  <span class="help abs">?</span>
</header>

<section class="hero abs" role="img" aria-label="Team of people collaborating around a desk">
</section>
<svg class="abs" style="left:390px;top:110px" width="260" height="240" viewBox="0 0 260 240" role="img" aria-label="Man in glasses reviewing documents inside a speech bubble">
  <defs><linearGradient id="heroPortrait" x1="0" y1="0" x2="0" y2="1"><stop offset="0" stop-color="#f3f1ee"/><stop offset="1" stop-color="#a69b91"/></linearGradient></defs>
  <path d="M140 2 A106 106 0 1 1 66 180 L12 220 L40 175 A106 106 0 0 1 140 2 Z" fill="url(#heroPortrait)" stroke="#f7941d" stroke-width="4"/>
</svg>
<div class="hero-title abs display">Convert more customers</div>
<div class="hero-sub abs">Experience the power of experts collaborating<br>on your project.</div>
<div class="hero-cta btn abs">GET STARTED</div>
<span class="hero-dot abs" style="left:57px"></span>
<span class="hero-dot abs" style="left:76px"></span>

<aside class="filters abs">
  <div class="filters-head btn abs">Filters<span class="filters-head-icon abs"></span></div>
  <div class="price-label abs">Price</div>
  <div class="price-tag abs">$ 80</div>
  <span class="abs" style="left:136px;top:48px;width:10px;height:10px;border:1px solid #999;border-radius:50%"></span>
  <div class="slider abs"><div class="slider-fill abs"></div></div>
  <div class="price-min abs">$ 10</div>
  <div class="filter-row abs" style="top:96px">Country<span class="plus">+</span></div>
  <div class="filter-row abs" style="top:128px">Categories<span class="plus">+</span></div>
  <div class="filter-row abs" style="top:160px">Time Left<span class="plus">+</span></div>
  <div class="filter-row abs" style="top:192px">Active &nbsp;|&nbsp; Expired<span class="plus">+</span></div>
  <div class="filter-row abs" style="top:224px">Contains Adult Content<span class="plus">+</span></div>
  <div class="filter-row abs" style="top:256px">Keywords<span class="plus">+</span></div>
  <div class="filter-row abs" style="top:288px">Followers<span class="plus">+</span></div>
  <div class="filter-row abs" style="top:320px">Types<span class="plus">+</span></div>
  <div class="filter-row abs" style="top:352px">Sorting<span class="plus">+</span></div>
</aside>
<div class="save btn abs">Save Filters</div>

<h2 class="section-title abs display" style="font-weight:400">Crowd <span>Projects</span></h2>
<div class="sort abs">
  <div class="sort-label abs">Sort By</div>
  <div class="sort-value abs">Price<svg class="abs" style="left:72px;top:8px" width="8" height="6" viewBox="0 0 8 6"><path d="M1 1l3 3 3-3" fill="none" stroke="#f7941d" stroke-width="1.2"/></svg></div>
</div>
<div class="sort-menu abs">
  <div class="sort-item">Country</div>
  <div class="sort-item is-active">Price</div>
  <div class="sort-item">Time left</div>
</div>

<article class="card is-first abs" style="top:443px;height:143px">
  <div class="card-photo abs" role="img" aria-label="Businesswoman portrait" style="background:linear-gradient(#ececec,#b8b8b8)"></div>
  <svg class="card-wedge abs" width="40" height="20" viewBox="0 0 40 20"><path d="M0 20 L26 2 L40 20 Z" fill="#f7941d"/></svg>
  <div class="card-price abs">$ 80<br><span style="font-size:9px">U.K</span></div>
  <div class="card-title abs">Morbi in ante arcu Maecenas sit an</div>
  <div class="card-time abs">Time Left : 6 days</div>
  <p class="card-body abs">Beatae vitae dicta sunt explicabo. Nemo enim ipsam voluptatem quia voluptas sit aspernatur aut odit aut fugit, sed quia consequuntur magni dolores eos qui ratione voluptatem sequi nesciunt. Neque porro quisquam est , qui dolorem ipsum quia dolor sit amet, consectetur, adipisci velit, sed quia.</p>
</article>

<article class="card abs" style="top:585px;height:161px">
  <div class="card-photo abs" role="img" aria-label="Two business colleagues portrait" style="background:linear-gradient(#e4e4e4,#8e8e8e)"></div>
  <svg class="card-wedge abs" width="40" height="20" viewBox="0 0 40 20"><path d="M0 20 L26 2 L40 20 Z" fill="#f7941d"/></svg>
  <div class="card-price abs">$ 90<br><span style="font-size:9px">CA</span></div>
  <div class="card-title abs">Lorem ipsum dolor sit amet, consectetur adipiscing</div>
  <div class="card-time abs">Time Left : 6 days</div>
  <p class="card-body abs">Beatae vitae dicta sunt explicabo. Nemo enim ipsam voluptatem quia voluptas sit aspernatur aut odit aut fugit, sed quia consequuntur magni dolores eos qui ratione voluptatem sequi nesciunt. Neque porro quisquam est , qui dolorem ipsum quia dolor sit amet, consectetur, adipisci velit, sed quia.</p>
</article>

<article class="card abs" style="top:745px;height:158px">
  <div class="card-photo abs" role="img" aria-label="Smiling businesswoman portrait" style="background:linear-gradient(#efefef,#9a8f88)"></div>
  <svg class="card-wedge abs" width="40" height="20" viewBox="0 0 40 20"><path d="M0 20 L26 2 L40 20 Z" fill="#f7941d"/></svg>
  <div class="card-price abs">$ 250<br><span style="font-size:9px">U.S</span></div>
  <div class="card-title abs">Neque porro quisquam est qui dolorem ipsum</div>
  <div class="card-time abs">Time Left : 6 days</div>
  <p class="card-body abs">Beatae vitae dicta sunt explicabo. Nemo enim ipsam voluptatem quia voluptas sit aspernatur aut odit aut fugit, sed quia consequuntur magni dolores eos qui ratione voluptatem sequi nesciunt. Neque porro quisquam est , qui dolorem ipsum quia dolor sit amet, consectetur, adipisci velit, sed quia.</p>
</article>

<nav class="pager abs">
  <span style="color:#999;font-weight:400">«</span><span>1</span><span>2</span><span>3</span><span>4</span><span>5</span><span>6</span><span class="is-current">7</span><span>8</span><span>9</span><span style="color:#999;font-weight:400">»</span>
</nav>
<div class="pager-line abs"></div>
<svg class="abs" style="left:579px;top:928px" width="6" height="5" viewBox="0 0 6 5"><path d="M0 5 L3 0 L6 5Z" fill="#2a2a2a"/></svg>

<section class="testimonials abs" role="img" aria-label="Smiling woman behind an orange overlay">
  <h3 class="t-title abs display" style="font-weight:400">Client Testmonials</h3>
  <p class="t-quote abs"><span class="t-mark" style="margin-right:18px">“</span>Before you put any content in front of your audience, crowdsource it with<br>Pelmora, you won’t regret it <span class="t-mark" style="margin-left:10px">”</span></p>
  <svg class="abs" style="left:243px;top:110px" width="10" height="14" viewBox="0 0 10 14"><path d="M8 1 L2 7 L8 13" fill="none" stroke="#fff" stroke-width="2"/></svg>
  <svg class="abs" style="left:432px;top:110px" width="10" height="14" viewBox="0 0 10 14"><path d="M2 1 L8 7 L2 13" fill="none" stroke="#fff" stroke-width="2"/></svg>
  <div class="t-avatar abs" role="img" aria-label="Client portrait"></div>
  <div class="t-name abs">AARON VELL</div>
  <div class="t-role abs">CEO, TBA</div>
  <svg class="t-stars abs" width="42" height="8" viewBox="0 0 42 8">
    <g fill="#fff"><path id="star" d="M4 0l1 2.7 2.9.1-2.3 1.8.8 2.8L4 5.8 1.6 7.4l.8-2.8L.1 2.8 3 2.7z"/><use href="#star" x="11"/><use href="#star" x="22"/><use href="#star" x="33"/></g>
  </svg>
</section>

<footer class="footer abs">
  <div class="footer-links abs">About &nbsp;|&nbsp; Terms &nbsp;|&nbsp; Privacy Policy &nbsp;|&nbsp; All Rights Reserved. Copyrights © 2015.</div>
  <span class="social abs" style="left:556px"></span>
  <span class="social abs" style="left:576px"></span>
  <span class="social abs" style="left:596px"></span>
  <span class="social abs" style="left:617px"></span>
</footer>

</body>
</html>
```